Business card for Eyelash extension salon in Beverly Hills,California USA

We need new business card for our salon in Beverly Hills. The salon name is 'Lashvera' . We would like to have...Business name: Lashvera Name of person: will provide later Address 4720 N.Alder Crest Ave Beverly Hills , CA 90210 Phone: will provide later (Text only) Web: www.lashverastudio.example Snapgrid icon, Circlebook icon follow us for seasonal campaign and news @lashverastudiolounge Design should look elegant, high-end, clean, simple, cohesive with my brand. Please refer my brand board. Business name color will be metallic bronzy color. Im thinking grey background or white background. Thanks

Target Market(s)

25-35. Gender neutral. People who are in Entertainment business industry.
This is High-end Eyelash extension salon in Beverly Hills

Industry/Entity Type

Beauty Salon

Contact Information for Business Card

Business name: Lashvera
Name of person: will provide later
Address 4720 N.Alder Crest Ave Beverly Hills , CA 90210
Phone: will provide later (Text only)
Web: www.lashverastudio.example
Snapgrid icon, Circlebook icon
follow us for seasonal campaign and news @lashverastudiolounge

Requirements
Must have
• Beautiful, elegant, clean and simple look but very attractive and modern
Should not have
• We don't like too clutter, too busy designs.

```html
<!DOCTYPE html>
<html lang="en">
<head>
<meta charset="utf-8">
<title>Lashvera Business Card</title>
<link rel="stylesheet" href="https://fonts.googleapis.com/css2?family=Cormorant+Garamond:wght@400;500&family=Playfair+Display:wght@700&display=swap">
<style>
  :root {
    --bronze: #8a6a50;
    --backdrop: #2a2a2a;
    --ink: #3f3f3f;
    --muted: #b3b3b3;
    --rule: #8c8c8c;
    --white: #ffffff;
    --silver-edge: #b9b9b9;
  }
  html, body {
    margin: 0;
    padding: 0;
    overflow: hidden;
  }
  .stage {
    position: relative;
    width: 1200px;
    height: 960px;
    background: var(--backdrop);
    overflow: hidden;
    font-family: "Cormorant Garamond", Georgia, serif;
    font-variant-numeric: lining-nums;
  }
  .card {
    position: absolute;
    width: 600px;
    height: 343px;
    overflow: hidden;
    box-shadow: 0 3px 8px rgba(0,0,0,0.45);
  }
  .card-front {
    left: 302px;
    top: 122px;
    background:
      radial-gradient(ellipse 420px 300px at 78% 18%, #ffffff 0%, #f4f4f4 35%, rgba(255,255,255,0) 75%),
      linear-gradient(120deg, #dcdcdc 0%, #f2f2f2 45%, #d4d4d4 100%);
  }
  .brand-name {
    position: absolute;
    margin: 0;
    font-family: "Cormorant Garamond", Georgia, serif;
    font-weight: 500;
    line-height: 1;
  }
  .card-front .brand-name {
    right: 34px;
    top: 72px;
    font-size: 58px;
    color: var(--bronze);
  }
  .holder {
    position: absolute;
    left: 28px;
    top: 188px;
  }
  .holder-name {
    margin: 0;
    font-family: "Playfair Display", Georgia, serif;
    font-weight: 700;
    font-size: 22px;
    letter-spacing: 0.5px;
    color: var(--bronze);
    line-height: 1;
  }
  .holder-role {
    margin: 4px 0 0;
    font-family: "Playfair Display", Georgia, serif;
    font-weight: 700;
    font-size: 14px;
    color: var(--muted);
    letter-spacing: 0.3px;
  }
  .divider {
    position: absolute;
    left: 28px;
    top: 241px;
    width: 538px;
    height: 1px;
    background: var(--rule);
  }
  .contact-list {
    position: absolute;
    left: 28px;
    top: 254px;
    margin: 0;
    padding: 0;
    list-style: none;
    font-size: 16px;
    color: var(--ink);
    line-height: 20px;
  }
  .contact-list li {
    display: flex;
    align-items: center;
    gap: 8px;
  }
  .contact-list svg {
    width: 13px;
    height: 13px;
    fill: var(--bronze);
  }
  .address {
    position: absolute;
    right: 31px;
    top: 254px;
    margin: 0;
    font-style: normal;
    text-align: right;
    font-size: 16px;
    line-height: 20px;
    color: var(--ink);
  }
  .front-base {
    position: absolute;
    left: 0;
    top: 0;
    width: 600px;
    height: 343px;
  }
  .web {
    position: absolute;
    right: 26px;
    top: 314px;
    margin: 0;
    font-size: 16px;
    letter-spacing: 1px;
    color: var(--white);
  }
  .card-back {
    left: 299px;
    top: 495px;
    background: var(--bronze);
  }
  .card-back .brand-name {
    left: 0;
    right: 0;
    top: 116px;
    text-align: center;
    font-size: 84px;
    color: var(--white);
  }
  .social {
    position: absolute;
    left: 0;
    right: 0;
    top: 286px;
    display: flex;
    justify-content: center;
    align-items: center;
    gap: 10px;
    color: var(--white);
    font-size: 14px;
    letter-spacing: 1px;
  }
  .social-rule {
    width: 40px;
    height: 1px;
    background: var(--white);
  }
  .social-dot {
    width: 4px;
    height: 4px;
    border-radius: 50%;
    background: var(--white);
  }
</style>
</head>
<body>
<div class="stage">

  <section class="card card-front" aria-label="Business card front">
    <svg class="front-base" viewBox="0 0 600 343" aria-hidden="true">
      <rect x="0" y="336" width="600" height="7" fill="var(--bronze)"/>
      <polygon points="0,331 322,331 322,336 0,336" fill="#ffffff"/>
      <polygon points="320,336 350,309 588,309 588,343 320,343" fill="var(--bronze)"/>
      <rect x="591" y="309" width="9" height="34" fill="var(--silver-edge)"/>
    </svg>

    <h1 class="brand-name">Lashvera</h1>

    <div class="holder">
      <p class="holder-name">JORDAN HALE</p>
      <p class="holder-role">CEO/FOUNDER</p>
    </div>

    <div class="divider"></div>

    <ul class="contact-list">
      <li>
        <svg viewBox="0 0 24 24" aria-hidden="true"><path d="M6.6 10.8a15.1 15.1 0 0 0 6.6 6.6l2.2-2.2a1 1 0 0 1 1-.25 11.4 11.4 0 0 0 3.6.57 1 1 0 0 1 1 1V20a1 1 0 0 1-1 1A17 17 0 0 1 3 4a1 1 0 0 1 1-1h3.5a1 1 0 0 1 1 1c0 1.25.2 2.45.57 3.6a1 1 0 0 1-.25 1z"/></svg>
        555 014 7719
      </li>
      <li>
        <svg viewBox="0 0 24 24" aria-hidden="true"><path d="M2 5h20v14H2z" fill="var(--bronze)"/><path d="M3 6l9 6.3L21 6" fill="none" stroke="#eeeeee" stroke-width="1.6"/></svg>
        news@lashverastudiolounge
      </li>
    </ul>

    <address class="address">4720 N.Alder Crest Ave<br>Crestmoor Heights, CA 90452</address>

    <p class="web">www.lashverastudio.example</p>
  </section>

  <section class="card card-back" aria-label="Business card back">
    <h2 class="brand-name">Lashvera</h2>
    <div class="social">
      <span class="social-rule"></span>
      <span>Circlebook</span>
      <span class="social-dot"></span>
      <span>Snapgrid</span>
      <span class="social-rule"></span>
    </div>
  </section>

</div>
</body>
</html>
```